Cat-products company needs smart, yet endearing, business card

We need a business card design for a new, but up-and-running, business based in Honolulu, Hawaii. The business is Purrnest Nook Co. Our first product is the most environmentally-friendly cat grass kit ever seen on the planet. Future products, currently in the R&D phase, will include a variety of exciting cat scratchers. We also do consulting work to help apartment-dwellers make their home more cat-friendly and, in the future, plan on doing full, custom installs of structure to create high walkways for cats.

Target Market(s)

Middle-aged, apartment-dwelling, middle-class workers who own 1 or more cats and who dote on them.

Industry/Entity Type

Pet Care

Contact Information for Business Card

A striking, professional, yet warm and friendly design is what we're after.

Font styles to use
Serif
Sans Serif
Other font styles liked:
• Comfortaa

Colors

Designer to choose colors to be used in the design.

Requirements
Must have
• The company logo: (see attachment)
• The company name: Purrnest Nook Co
• The web address: www.purrnestnookco.com
• Email: support@purrnestnookco.com
• Phone: +1 (808) 571 6023
• Update (Fri Jun 30 3017 7:45pm Hawaii Time) I would like, is possible, uploaded picture of the cat grass kit on the back of the card with some text along the lines of: Purrnest Nook Co - Maker Of The Leafiest Feline Sprout Set Yet
Nice to have
• A cat picture, cartoon, real or silhouette that illustrates cats in action and/or relaxing; ie using the apartment space to live, play and relax in and being well-contented.
• Most of the website is done in the font: Comfortaa. It might be nice to continue using this for brand consistency.
Should not have
• Hard-to-read fonts.

```html
<!DOCTYPE html>
<html lang="en">
<head>
<meta charset="utf-8">
<title>Purrnest Nook Co — Business Card</title>
<link rel="stylesheet" href="https://fonts.googleapis.com/css2?family=Comfortaa:wght@400;700&display=swap">
<style>
  :root {
    --brown: #4e2c23;
    --yellow: #f6b01c;
    --cream: #f7e3b5;
    --card: #ffffff;
    --stage: #ece8e3;
    --tile-a: #4e2c23;
    --tile-b: #f6b01c;
  }
  * { box-sizing: border-box; margin: 0; padding: 0; }
  html, body { width: 1200px; height: 995px; overflow: hidden; }
  body {
    background: var(--stage);
    font-family: "Comfortaa", sans-serif;
    color: var(--brown);
    position: relative;
  }
  .card {
    position: absolute;
    top: 130px;
    width: 430px;
    height: 735px;
    background: var(--card);
    border-radius: 24px;
    overflow: hidden;
    box-shadow: 0 12px 30px rgba(60, 40, 30, .18);
  }
  .card--front { left: 140px; }
  .card--back { left: 630px; }

  .brand {
    display: flex;
    flex-direction: column;
    align-items: center;
    text-align: center;
  }
  .brand__mark {
    background: var(--brown);
    border-radius: 10px;
    flex: none;
  }
  .brand__name {
    font-weight: 700;
    color: var(--brown);
    line-height: 1.08;
    white-space: nowrap;
  }
  .brand__line { display: block; }

  /* front */
  .card--front .brand { margin-top: 78px; gap: 22px; }
  .card--front .brand__mark { width: 92px; height: 92px; }
  .card--front .brand__name { font-size: 50px; }
  .social {
    display: flex;
    justify-content: center;
    gap: 18px;
    margin-top: 30px;
  }
  .social__tile {
    width: 40px; height: 40px;
    border-radius: 8px;
    background: var(--tile-a);
  }
  .social__tile:nth-child(even) { background: var(--tile-b); }
  .tagline {
    margin: 22px 44px 0;
    text-align: center;
    font-size: 15px;
    line-height: 1.45;
    color: var(--brown);
  }
  .front__illustration {
    position: absolute;
    left: 0; right: 0;
    bottom: 62px;
    height: 228px;
    background:
      radial-gradient(ellipse 38% 42% at 30% 62%, var(--cream) 0%, rgba(247,227,181,0) 100%),
      linear-gradient(160deg, #f6b01c 0%, #e59a1a 40%, #6a3a28 75%, #4e2c23 100%);
    border-radius: 55% 45% 0 0 / 70% 80% 0 0;
  }
  .band {
    position: absolute;
    left: 0; right: 0; bottom: 0;
    height: 84px;
    background: var(--brown);
    border-top: 6px solid var(--yellow);
    display: flex;
    align-items: center;
    justify-content: center;
  }
  .band__web {
    color: var(--yellow);
    font-size: 21px;
    font-weight: 700;
    letter-spacing: .3px;
  }

  /* back */
  .card--back .brand { margin-top: 70px; gap: 18px; }
  .card--back .brand__mark { width: 80px; height: 80px; }
  .card--back .brand__name { font-size: 36px; }
  .person { text-align: center; margin-top: 58px; }
  .person__name { font-size: 32px; font-weight: 700; }
  .person__first { color: var(--yellow); }
  .person__role { font-size: 20px; margin-top: 6px; color: var(--brown); }
  .contact { margin: 48px 36px 0; text-align: center; }
  .contact__item { padding: 14px 0; }
  .contact__item + .contact__item { border-top: 1.5px solid var(--yellow); }
  .contact__label { font-size: 15px; font-weight: 700; color: var(--yellow); }
  .contact__value { font-size: 20px; margin-top: 6px; color: var(--brown); }
  .contact__value--email { font-size: 19px; }
</style>
</head>
<body>
  <section class="card card--front">
    <div class="brand">
      <span class="brand__mark"></span>
      <span class="brand__name"><span class="brand__line">Purrnest</span><span class="brand__line">Nook Co</span></span>
    </div>
    <div class="social">
      <span class="social__tile"></span>
      <span class="social__tile"></span>
      <span class="social__tile"></span>
      <span class="social__tile"></span>
    </div>
    <p class="tagline">Purrnest Nook Co - Maker Of The Leafiest Feline Sprout Set Yet</p>
    <div class="front__illustration" role="img" aria-label="Cartoon of a striped orange and brown tabby cat lying down, resting on the card's lower band"></div>
    <div class="band"><span class="band__web">www.purrnestnookco.com</span></div>
  </section>

  <section class="card card--back">
    <div class="brand">
      <span class="brand__mark"></span>
      <span class="brand__name">Purrnest Nook Co</span>
    </div>
    <div class="person">
      <p class="person__name"><span class="person__first">Employee</span> Name</p>
      <p class="person__role">Manager</p>
    </div>
    <div class="contact">
      <div class="contact__item">
        <p class="contact__label">Phone</p>
        <p class="contact__value">+1 (808) 571 6023</p>
      </div>
      <div class="contact__item">
        <p class="contact__label">Email</p>
        <p class="contact__value contact__value--email">support@purrnestnookco.com</p>
      </div>
    </div>
    <div class="band"><span class="band__web">www.purrnestnookco.com</span></div>
  </section>
</body>
</html>
```